International Manufacturing Business Needs A Heavy Hitting Wordpress Design!

We need wordpress template designs for a new website for our UK based International company Dalvesham Engineering Ltd. We manufacture and supply steel security doors and window units. We would like designs that feature the black and yellow industrial "stripes" that can be seen at our current site www.dalvoportals.com. The final design should communicate strength, power and weight to represent the quality of the products and the security that they provide.

It feels like we need 3 different types of page to be able to be created as per the current website at www.dalvosafeportals.com.

Homepage
Products/Accessories
Leadtimes/Downloads/Contact

It may be that 3 different page types can be created with one template. I'm totally open to this.

I don't like the way that the site currently handles product images, nobody wants to click on even thumbnail to see the product. http://dalvosafeportals.com/products/personnel-doors/

Totally open to suggestions on layout to enable the feeling outlined in the brief above.

Please ask if anything is not clear or you need answers to drill down on specifics.

Sick

Target Market(s)

Businesses that buy steel doors

Font styles to use
Sans Serif
Other font styles liked:
• Copperplate Gothic Bold - For Company Name but we are open to suggestions

Colors

Designer to choose colors to be used in the design.

Requirements
Must have
• Professional looking, clean design
• Conveys strength, power and weight to represent the quality of the products, the characteristics of steel and the security that they provide.
• Incorporates black and yellow stripes of our branding
• Ability to create pages with content as seen at www.dalvosafeportals.com
• A better way of showing the product images
Nice to have
• If possible. a design that gives off the feeling that not only do we supply the products we also make them in house too. I don't know what this looks like but a way of differentiating between a supply only business and one that manufacturers the product too.
Should not have
• We don't like the current thumbnail method of showing the product images

```html
<!DOCTYPE html>
<html lang="en">
<head>
<meta charset="utf-8">
<title>Dalvesham Engineering Ltd – Steel Security Doors</title>
<link href="https://fonts.googleapis.com/css2?family=Poppins:wght@400;500;600;700&display=swap" rel="stylesheet">
<style>
:root{
  --yellow:#ffe500;
  --black:#000;
  --ink:#111;
  --footer:#232323;
  --grey:#b9b9b9;
  --text:#333;
  --white:#fff;
  --stripe:repeating-linear-gradient(-45deg,var(--ink) 0 22px,var(--yellow) 22px 44px);
  --stripe-small:repeating-linear-gradient(-45deg,var(--ink) 0 6px,var(--yellow) 6px 12px);
}
*{margin:0;padding:0;box-sizing:border-box}
html,body{width:1200px;height:3822px;overflow:hidden}
body{position:relative;font-family:'Poppins',sans-serif;background:var(--white);color:var(--text)}
.abs{position:absolute}
.band{position:absolute;left:0;width:1200px;background:var(--stripe)}
.mini-stripe{position:absolute;height:12px;background:var(--stripe-small)}
.heading{position:absolute;font-weight:700;font-size:26px;letter-spacing:.5px;text-transform:uppercase;line-height:1}

/* hero */
.hero{position:absolute;left:0;top:0;width:1200px;height:820px;background:var(--stripe)}
.hero-photo{position:absolute;left:38px;top:38px;width:1124px;height:782px;
  background:linear-gradient(180deg,#e9eef0 0%,#cfd8d6 35%,#b9b3aa 60%,#5a5450 100%)}
.logo{position:absolute;left:160px;top:72px;display:flex;align-items:center;gap:12px}
.logo-mark{width:34px;height:34px;background:#1a9b8a}
.logo-name{font-weight:600;font-size:20px;color:#222;line-height:1.05;width:230px}
.phone{position:absolute;left:842px;top:70px;font-weight:600;font-size:17px;color:#111}
.nav{position:absolute;left:482px;top:114px;display:flex;gap:24px;font-size:12px;font-weight:500;color:#111;text-transform:uppercase;list-style:none}
.nav li:first-child{font-weight:600}
.dots{position:absolute;left:574px;top:750px;display:flex;gap:8px}
.dots span{width:14px;height:14px;border-radius:50%;background:#111}
.dots span.on{background:var(--yellow)}

/* what we do */
.what{position:absolute;left:0;top:820px;width:1200px;height:658px;background:var(--black)}
.vlabel{position:absolute;transform:rotate(-90deg);transform-origin:left top;font-weight:600;font-size:15px;letter-spacing:2px;text-transform:uppercase;white-space:nowrap}
.what .vline{position:absolute;left:183px;top:128px;width:2px;height:428px;background:#333}
.what .vlabel{left:175px;top:400px;color:#333;background:var(--black);padding:0 10px}
.frame{position:absolute;border:6px solid var(--yellow)}
.photo{position:absolute}
.what-list{position:absolute;left:601px;top:220px;width:440px;list-style:none;color:#cfcfcf;font-size:12px;line-height:19px}
.what-list li{position:relative;padding-left:18px;margin-bottom:19px}
.what-list li::before{content:"";position:absolute;left:0;top:5px;width:7px;height:7px;border:1.5px solid var(--yellow);transform:rotate(45deg)}

/* our doors */
.doors{position:absolute;left:0;top:1503px;width:1200px;height:612px;background:var(--white)}
.door-item{position:absolute;left:160px;width:440px}
.door-item svg{position:absolute;left:0;top:0}
.door-item h3{position:absolute;left:90px;top:0;font-size:16px;font-weight:600;color:#111;text-transform:uppercase}
.door-item p{position:absolute;left:90px;top:30px;width:350px;font-size:12px;line-height:22px;color:#333}
.rule{position:absolute;left:160px;top:321px;width:440px;height:1px;background:#ccc}
.doors .vline{position:absolute;left:1009px;top:110px;width:2px;height:425px;background:#111}
.doors .vlabel{left:999px;top:378px;color:#111;background:var(--white);padding:0 10px}

/* accessories */
.acc{position:absolute;left:0;top:2145px;width:1200px;height:581px;background:var(--black)}
.grid{position:absolute;left:163px;top:110px;width:426px;height:382px;display:grid;grid-template-columns:1fr 1fr;grid-template-rows:1fr 1fr;gap:4px}
.acc p{position:absolute;left:655px;top:235px;width:455px;font-size:12px;line-height:26px;color:#fff}

/* latest products */
.latest{position:absolute;left:0;top:2726px;width:1200px;height:663px;background:var(--stripe)}
.latest-inner{position:absolute;left:38px;top:40px;width:1124px;height:585px;background:var(--yellow)}
.products{position:absolute;left:0;top:2958px;width:1200px;display:flex;justify-content:center;gap:76px}
.product{width:242px;text-align:center}
.circle{width:242px;height:242px;border-radius:50%;border:10px solid #8b8b8b;overflow:hidden}
.circle div{width:100%;height:100%}
.product h4{margin-top:28px;font-size:18px;font-weight:600;color:#111}
.product p{margin-top:8px;font-size:12px;line-height:24px;color:#222}

/* footer */
.footer{position:absolute;left:0;top:3389px;width:1200px;height:369px;background:var(--footer);color:#ddd}
.fcol{position:absolute;top:86px;font-size:12px;line-height:23px}
.fcol h5{font-size:15px;font-weight:500;color:#fff;margin-bottom:8px}
.fcol ul{list-style:none}
.fcol .link{color:var(--yellow)}
.social{display:flex;gap:14px;margin-top:6px}
.social span{width:9px;height:9px;border-radius:50%;background:var(--yellow)}
.to-top{position:absolute;left:1091px;top:271px;width:60px;height:60px;border-radius:50%;background:var(--yellow)}
.bottom{position:absolute;left:0;top:3758px;width:1200px;height:64px;background:var(--yellow);font-size:12px;color:#111}
.bottom .copy{position:absolute;left:0;width:1200px;top:22px;text-align:center}
.bottom .code{position:absolute;left:1080px;top:22px}
</style>
</head>
<body>

<header class="hero">
  <div class="hero-photo" role="img" aria-label="Bright living room with sofa and armchairs beside tall windows"></div>
  <div class="logo"><span class="logo-mark"></span><span class="logo-name">DALVESHAM ENGINEERING LTD.</span></div>
  <div class="phone">Ph: +44 (0)1632 960 300</div>
  <ul class="nav"><li>Home</li><li>Products</li><li>Accessories</li><li>Delivery &amp; Lead Times</li><li>Downloads</li><li>Contact</li></ul>
  <div class="dots"><span></span><span class="on"></span><span></span></div>
</header>

<section class="what">
  <div class="vline"></div>
  <div class="vlabel">What we do</div>
  <div class="frame" style="left:247px;top:148px;width:291px;height:418px"></div>
  <div class="photo" role="img" aria-label="Yellow front door in a porch" style="left:229px;top:130px;width:293px;height:418px;background:linear-gradient(90deg,#3c4650 0%,#6f7a82 25%,#d7cf2a 35%,#e2d733 75%,#8a8f94 100%)"></div>
  <h2 class="heading" style="left:599px;top:165px;color:var(--yellow)">What we do</h2>
  <div class="mini-stripe" style="left:777px;top:172px;width:212px"></div>
  <ul class="what-list">
    <li>Dalvesham security doors combine a high level of security with exceptional value.</li>
    <li>Our superior quality and proven reliability has made us the first choice for a wide range of companies no matter what their requirement or application.</li>
    <li>All of our products are designed and manufactured to the highest specification, combine this with a rigorous quality control system and an extensive after-sales service and it is easy to see why we are seen as industry leaders.</li>
    <li>We place particular emphasis on continuous development and twelve years experience ensures that we are always ahead of the competition and that we can react quickly to customer's requirements.</li>
    <li>Each and every Dalvesham product is subject to our fifty point quality control process before it is dispatched.</li>
    <li>Dalvesham have forged a reputation for affordable, high quality steel doors.</li>
  </ul>
</section>
<div class="band" style="top:1478px;height:25px"></div>

<section class="doors">
  <h2 class="heading" style="left:160px;top:105px;color:#111">Our doors</h2>
  <div class="mini-stripe" style="left:326px;top:112px;width:209px"></div>
  <div class="door-item" style="top:174px">
    <svg width="76" height="82" viewBox="0 0 76 82" fill="none" stroke="#111" stroke-width="2.5">
      <circle cx="14" cy="18" r="11"/><circle cx="14" cy="18" r="4"/>
      <path d="M14 29v44M14 50h8M14 60h6"/>
      <path d="M34 10l20-6 20 12v56H34z"/><circle cx="54" cy="18" r="3"/>
      <path d="M42 32h24M42 42h24M42 52h24M42 62h18"/>
    </svg>
    <h3>Security Doors</h3>
    <p>Sed ut perspiciatis unde omnis iste natus error sit voluptatem doloremque laudantium, totam rem ape veritatis et quasi archite cto beatae vitae dicta sunt explicabo.</p>
  </div>
  <div class="rule"></div>
  <div class="door-item" style="top:365px">
    <svg width="76" height="80" viewBox="0 0 76 80" fill="none" stroke="#111" stroke-width="2.5">
      <rect x="4" y="4" width="68" height="72"/>
      <path d="M4 18h68"/><rect x="22" y="8" width="32" height="7"/>
      <path d="M36 18v58"/><circle cx="30" cy="50" r="2.5"/><circle cx="42" cy="50" r="2.5"/>
    </svg>
    <h3>Fire Exit Doors</h3>
    <p>Sed ut perspiciatis unde omnis iste natus error sit voluptatem doloremque laudantium, totam rem ape veritatis et quasi archite cto beatae vitae dicta sunt explicabo.</p>
  </div>
  <div class="frame" style="left:668px;top:140px;width:288px;height:406px"></div>
  <div class="photo" role="img" aria-label="Poster of a red steel door showing its ten point locking system" style="left:647px;top:117px;width:255px;height:406px;border-radius:0 24px 0 0;background:linear-gradient(135deg,#1b1b1b 0%,#2a2a2a 30%,#b3161a 45%,#c81d22 60%,#1b1b1b 75%,#f1e22a 100%)"></div>
  <div class="vline"></div>
  <div class="vlabel">Our doors</div>
</section>
<div class="band" style="top:2115px;height:30px"></div>

<section class="acc">
  <div class="grid">
    <div role="img" aria-label="Grey panel door in a light room" style="background:linear-gradient(90deg,#ecebe8,#8f8a84 50%,#efeeeb)"></div>
    <div role="img" aria-label="Red door against a pale wall" style="background:linear-gradient(90deg,#e6e3df,#b2202a 45%,#b2202a 60%,#e4e0da)"></div>
    <div role="img" aria-label="White panel door in a beige room" style="background:linear-gradient(90deg,#b8b2aa,#f2f1ee 50%,#c9c3ba)"></div>
    <div role="img" aria-label="White door in a blue grey room" style="background:linear-gradient(90deg,#7f949a,#f1f1ef 55%,#8ea1a6)"></div>
  </div>
  <h2 class="heading" style="left:655px;top:182px;color:var(--yellow)">Accessories</h2>
  <div class="mini-stripe" style="left:841px;top:189px;width:191px"></div>
  <p>Lorem ipsum dolor sit amet, consectetur adipiscing elit, sed do eiusmod tempor incididunt ut labore et dolore mLorem ipsum dolor sit ametlora consectetur adipiscing elit, sed do eiusmod tempor incididunt ut labore et dolore maLorem ipsum dolor sit amet, consectetur adipiscing elit, eius mod tempor incididunt ut labore et dolore maLorem ipsum dolor sit amet, consectetur adipiscing elit, sed do eiusmod tempor incididunt ut labore et dolore maa</p>
</section>

<section class="latest">
  <div class="latest-inner"></div>
  <h2 class="heading" style="left:0;width:1200px;text-align:center;top:116px;color:#111">Our latest products</h2>
  <div class="mini-stripe" style="left:492px;top:166px;width:216px"></div>
</section>
<div class="products">
  <div class="product">
    <div class="circle"><div role="img" aria-label="Open white door letting in bright light" style="background:linear-gradient(90deg,#3f5964,#f7f7f2 45%,#dcdcd6 70%,#4a6470)"></div></div>
    <h4>Cloaking Frames</h4>
    <p>Lorem ipsumlorem dolor sit amet, consus cing elit, sed do eiusmod tempor</p>
  </div>
  <div class="product">
    <div class="circle"><div role="img" aria-label="Navy blue door in a pale room" style="background:linear-gradient(90deg,#ecebea,#2f4866 40%,#2f4866 62%,#e7e6e4)"></div></div>
    <h4>Anti-Vandal Shroud</h4>
    <p>Lorem ipsumlorem dolor sit amet, consus cing elit, sed do eiusmod tempor</p>
  </div>
  <div class="product">
    <div class="circle"><div role="img" aria-label="White panel door in a bright room" style="background:linear-gradient(90deg,#d9d8d4,#fbfbfa 50%,#cfcdc8)"></div></div>
    <h4>Personnel Doors</h4>
    <p>Lorem ipsumlorem dolor sit amet, consus cing elit, sed do eiusmod tempor</p>
  </div>
</div>

<footer class="footer">
  <div class="fcol" style="left:160px">
    <h5>Information</h5>
    <ul><li>+44 (0)1632 960 300</li><li>sales@dalvoportals.com</li><li class="link">Online order form</li></ul>
    <div class="social"><span></span><span></span><span></span><span></span></div>
  </div>
  <div class="fcol" style="left:364px">
    <h5>Useful Links</h5>
    <ul><li>Door Construction</li><li>Standard Features</li><li>Certification &amp; Testing</li><li>Threshold Specification</li><li>Size Specification</li><li>Internal/External Opening</li></ul>
  </div>
  <div class="fcol" style="left:606px">
    <h5>What We Do</h5>
    <ul><li>Onsectetur adipiscing eli</li><li>Sed do eiusmod tempo</li><li>Diduni ut</li><li>Onsectetur adipiscing eli</li><li>Sed do eiusmod tempo</li><li>Diduni ut</li></ul>
  </div>
  <div class="fcol" style="left:871px">
    <h5>Other Links</h5>
    <ul><li>Lorem ipsum dolor sit amet</li><li>consectetur adipiscing eli</li><li>sed do eiusmod tempo</li><li>incididunt ut labore et dolore</li><li>Magna aliqua</li><li>Ut enim ad minim venia</li></ul>
  </div>
  <div class="to-top">
    <svg width="60" height="60" viewBox="0 0 60 60" fill="none" stroke="#111" stroke-width="3"><path d="M30 42V18M21 27l9-9 9 9"/></svg>
  </div>
</footer>
<div class="bottom">
  <div class="copy">© 2018 All Rights are Reserved. &nbsp;Privacy Policy | Terms of Use</div>
  <div class="code">C4</div>
</div>

</body>
</html>
```